KAJU Freightways #ALLKAJU Business Cards & Letterhead

I am looking to business cards designed for our organization. We are currently undergoing a small re-branding that is taking place. Our organization is called KAJU Freightways and we are headquartered in Phoenix, AZ. We primarily provide transportation and logistics services to the Marlow Parcel Bureau who is our largest customer. I would like to see a design that incorporates name, title, contact info, website, and address (this will be different depending on the employee). I would also like to see some color on the business card using our logo colors or a variation. I would like our logo on the back of the business card with the website displayed. The final design should communicate that we are a next generation transportation operate that focuses on being driver-first, customer-centric, innovative, and sustainable.We would also like our #ALLKAJU catch phrase incorporated as well.

Target Market(s)

Transportation & Logistics

Industry/Entity Type

Trucking Company

Contact Information for Business Card

-First and Last Name
-Position Title
-Contact Phone
-Contact Email
-Physical Address

Font styles to use
Serif

Colors

Designer to choose colors to be used in the design.

Requirements
Must have
• -KAJU logo prominently displayed
• -#ALLKAJU catch phrase used
• -Some amount of color, design gradient, etc.
• -Logo on the back with website listed (https://www.kajufreightco.example)

```html
<!DOCTYPE html>
<html lang="en">
<head>
<meta charset="utf-8">
<title>KAJU Freightways Business Card</title>
<link href="https://fonts.googleapis.com/css2?family=Lato:wght@400;700;900&display=swap" rel="stylesheet">
<style>
  :root {
    --teal-deep: #053c47;
    --leaf-green: #7cc242;
    --paper: #f3f3f3;
    --stage: #3a3a3a;
    --divider: #cfcfcf;
    --white: #ffffff;
  }
  * { margin: 0; padding: 0; box-sizing: border-box; }
  html, body { width: 1200px; height: 1015px; overflow: hidden; }
  body {
    background: var(--stage);
    font-family: "Lato", sans-serif;
    position: relative;
  }
  .card {
    position: absolute;
    left: 250px;
    width: 700px;
    height: 400px;
    box-shadow: 0 14px 30px rgba(0,0,0,0.45);
    overflow: hidden;
  }
  .card-back {
    top: 70px;
    background: var(--teal-deep);
  }
  .card-front {
    top: 540px;
    background: var(--paper);
  }

  /* wordmark */
  .wordmark {
    position: absolute;
    display: flex;
    align-items: center;
    gap: 14px;
    font-weight: 900;
    font-size: 64px;
    letter-spacing: 1px;
    line-height: 1;
  }
  .wordmark-dot {
    width: 18px; height: 18px;
    border-radius: 50%;
    background: var(--leaf-green);
  }
  .card-back .wordmark {
    left: 50%; top: 150px;
    transform: translateX(-50%);
    color: var(--white);
  }
  .website {
    position: absolute;
    left: 0; right: 0;
    top: 322px;
    text-align: center;
    color: var(--leaf-green);
    font-size: 18px;
    letter-spacing: 0.3px;
  }

  .card-front .wordmark {
    left: 60px; top: 140px;
    color: var(--teal-deep);
  }
  .divider {
    position: absolute;
    left: 330px; top: 50px;
    width: 1px; height: 240px;
    background: var(--divider);
  }
  .contact {
    position: absolute;
    left: 362px; top: 62px;
    color: var(--teal-deep);
  }
  .person-name {
    font-weight: 900;
    font-size: 25px;
    letter-spacing: 0.5px;
    text-transform: uppercase;
    line-height: 1.1;
  }
  .person-title {
    color: var(--leaf-green);
    font-size: 19px;
    margin-bottom: 14px;
  }
  .contact-line {
    display: flex;
    align-items: center;
    gap: 8px;
    font-size: 17px;
    line-height: 1.45;
  }
  .contact-line svg { width: 18px; height: 18px; flex: none; }
  .company {
    margin-top: 14px;
    font-weight: 900;
    font-size: 18px;
  }
  .address {
    font-size: 17px;
    line-height: 1.3;
  }
  .tag-band {
    position: absolute;
    left: 0; right: 0; bottom: 0;
    height: 62px;
    background: var(--teal-deep);
  }
  .hashtag {
    position: absolute;
    left: 440px; top: 18px;
    color: var(--leaf-green);
    font-size: 22px;
    letter-spacing: 0.5px;
  }
</style>
</head>
<body>

  <section class="card card-back" aria-label="Card back">
    <div class="wordmark"><span class="wordmark-dot"></span>KAJU</div>
    <p class="website">www.kajufreightco.example</p>
  </section>

  <section class="card card-front" aria-label="Card front">
    <div class="wordmark"><span class="wordmark-dot"></span>KAJU</div>
    <div class="divider"></div>
    <div class="contact">
      <p class="person-name">Marcus Delane</p>
      <p class="person-title">Managing Director</p>
      <p class="contact-line">
        <svg viewBox="0 0 18 18" aria-hidden="true">
          <circle cx="9" cy="9" r="8" fill="none" stroke="#7cc242" stroke-width="1.8"/>
          <path d="M5.5 7.5c.4 2.4 2.6 4.6 5 5l1.3-1.4-1.7-1-1 .6c-.8-.4-1.4-1-1.8-1.8l.6-1-1-1.7z" fill="#053c47"/>
        </svg>
        044-555 018 224
      </p>
      <p class="contact-line">
        <svg viewBox="0 0 18 18" aria-hidden="true">
          <circle cx="9" cy="9" r="8" fill="none" stroke="#7cc242" stroke-width="1.8"/>
          <rect x="5" y="6" width="8" height="6" fill="#053c47"/>
          <path d="M5 6l4 3.2L13 6" fill="none" stroke="#f3f3f3" stroke-width="1"/>
        </svg>
        hello@kajufreightco.example
      </p>
      <p class="company">KAJU Freightways</p>
      <p class="address">421, Address line here<br>Country Name, 45452</p>
    </div>
    <div class="tag-band">
      <p class="hashtag">#ALLKAJU</p>
    </div>
  </section>

</body>
</html>
```